Bright Net Rally Website Design (design layout only)

We need a website design for a new nonprofit organization based in Des Moines, Iowa called Bright Net Rally. The nonprofit provides soccer training opportunities to youth soccer players looking to improve their game while also affecting the lives of the less fortunate in a positive way. While participating in the training programs the players also go out and raise money for selected charities. The organization then donates the funds. In its first 18 months we donated $10,500. We would like to see designs attempt to symbolize the mission of the nonprofit - essentially "improve you while improving someone else."

We would like to see the following features:

· A place to donate - Our intent is to have the home page linked to the donation page; a simple straight-forward process for people to give money, and make donating as painless as possible - no account needed to make a donation, credit card or e-check should be the only information needed to donate, and have it be on a single page.

· A photo gallery so people can browse the photo gallery to get a better understanding of our organization and a place to add videos and a calendar to show upcoming events

· A place for contact information and the profiles of directors and board members. This should include a spot showing all the charities the organization donates to. Also includes a news section/blog for comments and suggestions.

We want the design to revolve around the content and mission. We would really like to stress our organization as nonprofit. We would also like if the website was user friendly and easy to navigate.

The logo of our organization is uploaded

```html
<!DOCTYPE html>
<html lang="en">
<head>
<meta charset="utf-8">
<title>Bright Net Rally — Home</title>
<link href="https://fonts.googleapis.com/css2?family=Quicksand:wght@400;500;700&family=Open+Sans:wght@400;600&display=swap" rel="stylesheet">
<style>
:root{
  --green:#8cb84a;
  --green-dark:#6f9a33;
  --green-pale:#d3e5ad;
  --green-soft:#e6f0d2;
  --olive:#a9bf7d;
  --page:#f1f1ef;
  --white:#ffffff;
  --ink:#3d3d3d;
  --muted:#8a8a8a;
  --btn:#444444;
  --line:#e2e2e2;
}
*{box-sizing:border-box;margin:0;padding:0}
html,body{width:1200px;height:2452px;overflow:hidden}
body{position:relative;background:var(--page);font-family:"Open Sans",Arial,sans-serif;color:var(--ink);font-size:11px;line-height:1.5}
.backdrop{position:absolute;inset:0;width:1200px;height:2452px}
.block{position:absolute}
.panel{background:var(--white);box-shadow:0 1px 4px rgba(0,0,0,.12)}
.photo{display:block}
h2,h3,.nav a,.btn,.brand-name{font-family:"Quicksand",Arial,sans-serif}

/* header */
.site-header{left:180px;top:32px;width:840px;height:88px;background:var(--white);display:flex;align-items:center;justify-content:space-between;padding:0 24px}
.brand{display:flex;align-items:center;gap:8px}
.brand-mark{width:22px;height:22px;background:var(--green)}
.brand-name{font-size:17px;font-weight:700;color:var(--green-dark)}
.nav{display:flex;align-items:center;gap:4px}
.nav a{font-size:12px;font-weight:700;color:var(--ink);text-decoration:none;padding:6px 10px;text-transform:uppercase}
.nav a.active{color:var(--green-dark)}
.nav .donate{background:var(--green);color:var(--white);border-radius:3px;padding:6px 12px}

/* hero */
.hero{left:180px;top:120px;width:840px;height:392px;background:linear-gradient(180deg,#cfd8c6 0%,#a6b98a 45%,#5f8a2f 100%)}
.hero-copy{position:absolute;right:36px;top:140px;text-align:right;color:var(--white)}
.hero-copy p{font-family:"Quicksand",sans-serif;font-size:17px;font-weight:700;letter-spacing:.5px}
.hero-copy h1{font-family:"Quicksand",sans-serif;font-size:32px;font-weight:500;color:var(--green-pale);line-height:1}
.hero-copy .btn{margin-top:14px}
.dots{position:absolute;left:50%;bottom:14px;display:flex;gap:6px;transform:translateX(-50%)}
.dots span{width:8px;height:8px;border-radius:50%;background:rgba(255,255,255,.6)}
.dots span:first-child{background:var(--white)}

.btn{display:inline-block;background:var(--btn);color:var(--white);font-size:12px;font-weight:700;padding:7px 14px;border-radius:2px}
.btn.green{background:var(--green)}

.bar{height:40px;background:var(--green);color:var(--white);font-family:"Quicksand",sans-serif;font-size:18px;font-weight:700;padding:8px 14px}

/* blog */
.blog{left:180px;top:552px;width:508px;height:680px}
.post{display:flex;gap:16px;padding:18px 16px;border-bottom:1px solid var(--line);height:184px}
.post .photo{width:150px;height:104px;flex:none}
.post p{color:var(--green-dark);font-size:12px;line-height:1.6}
.post .meta{display:flex;align-items:center;gap:10px;margin-top:10px;color:var(--ink);font-size:10px}
.post .meta .btn{font-size:10px;padding:4px 8px}
.blog .more{position:absolute;right:14px;bottom:14px}

/* news */
.news{left:708px;top:552px;width:312px;height:444px}
.news-item{display:flex;gap:12px;padding:18px 14px 10px}
.news-item .photo{width:64px;height:54px;flex:none}
.news-item p{color:var(--green-dark);font-size:11px}
.news-item small{display:block;color:var(--muted);font-size:9px;margin-top:2px}
.news .more{position:absolute;right:0;bottom:0}

.appeal{left:708px;top:1012px;width:312px;height:220px;background:linear-gradient(180deg,#cfe7f2,#a7d38a)}
.appeal-copy{position:absolute;right:16px;top:36px;width:150px;font-size:11px;color:var(--green-dark)}
.appeal-copy .btn{margin-top:10px}

/* section titles */
.section-title{font-size:20px;font-weight:700;color:var(--green-dark)}

/* videos */
.videos-title{left:180px;top:1256px}
.videos{left:180px;top:1290px;width:508px;height:420px;background:var(--olive);padding:12px}
.video-main{position:relative;width:484px;height:266px;background:linear-gradient(135deg,#c89b6a,#5b8fb7 60%,#d6a43a)}
.play{position:absolute;left:50%;top:50%;width:56px;height:56px;margin:-28px 0 0 -28px}
.video-thumbs{display:flex;gap:14px;margin-top:14px;justify-content:center}
.video-thumbs .photo{width:88px;height:64px;border:3px solid var(--white)}
.videos .btn{position:absolute;left:50%;bottom:14px;transform:translateX(-50%)}

/* gallery */
.gallery-title{left:708px;top:1256px}
.gallery{left:708px;top:1290px;width:312px;height:320px;padding:0}
.gallery-main{position:relative;width:312px;height:180px;background:linear-gradient(180deg,#c6d6e4 0%,#8db35a 60%,#5f8a2f)}
.arrow{position:absolute;top:70px;width:28px;height:40px;background:var(--btn)}
.arrow.prev{left:0}.arrow.next{right:0}
.gallery-grid{display:grid;grid-template-columns:repeat(5,1fr);gap:6px;padding:10px}
.gallery-grid .photo{height:52px}

/* board */
.board-title{left:0;top:1740px;width:1200px;text-align:center;font-size:22px;font-weight:500;color:var(--green-dark)}
.board{left:180px;top:1792px;width:840px;display:flex;justify-content:space-between}
.member{width:126px;text-align:center}
.member .photo{width:126px;height:112px;background:linear-gradient(180deg,#d8d3cc,#9ea3a8)}
.member h3{font-size:11px;font-weight:700;margin-top:8px}
.member small{display:block;color:var(--green-dark);font-size:9px}

/* footer */
.footer{left:180px;top:2100px;width:840px;height:290px;display:flex;gap:40px}
.col{flex:1}
.col h3{font-size:13px;font-weight:700;color:var(--green-dark);margin-bottom:14px}
.col ul{list-style:none}
.col li{font-size:10px;margin-bottom:18px}
.event{display:flex;gap:8px;margin-bottom:14px}
.event .date{width:14px;height:14px;background:var(--green);flex:none;margin-top:2px}
.event p{font-size:10px;color:var(--green-dark)}
.contact p{font-size:10px;margin-bottom:6px}
.map{width:190px;height:130px;background:linear-gradient(135deg,#eceae4,#d9dfe6)}
.copyright{left:0;top:2414px;width:1200px;text-align:center;font-size:10px;color:var(--muted)}
</style>
</head>
<body>

<svg class="backdrop" viewBox="0 0 1200 2452" aria-hidden="true">
  <polygon points="0,0 560,0 0,300" fill="#d3e5ad"/>
  <polygon points="760,0 1200,0 1200,420" fill="#d3e5ad"/>
  <polygon points="0,2060 1200,1980 1200,2452 0,2452" fill="#ffffff"/>
  <polygon points="0,1990 1200,1920 1200,1990 0,2060" fill="#b8d283"/>
</svg>

<header class="block site-header">
  <div class="brand"><span class="brand-mark"></span><span class="brand-name">Bright Net Rally</span></div>
  <nav class="nav">
    <a class="active">Home</a><a>About Us</a><a>Training Programs</a><a>Events</a><a>FAQs</a><a>Contact Us</a><a class="donate">Donate</a>
  </nav>
</header>

<section class="block hero" role="img" aria-label="Photo of a soccer ball on a grass pitch with players in the background">
  <div class="hero-copy">
    <p>WE ARE A NON PROFIT</p>
    <h1>ORGANISATION</h1>
    <span class="btn">Learn more</span>
  </div>
  <div class="dots"><span></span><span></span><span></span></div>
</section>

<section class="block panel blog">
  <div class="bar">Blog</div>
  <article class="post">
    <div class="photo" role="img" aria-label="Youth players training on the field" style="background:linear-gradient(135deg,#9fc46a,#4f7d2a)"></div>
    <div><p>Our spring camp brought forty young players together to sharpen skills and raise funds for local food banks across the city this season.</p>
    <div class="meta"><span class="btn">Read More</span><span>No Comments</span></div></div>
  </article>
  <article class="post">
    <div class="photo" role="img" aria-label="Players running drills on the pitch" style="background:linear-gradient(135deg,#7fa7c9,#6f9a33)"></div>
    <div><p>Every drill counts twice: players improve their game while each session helps a chosen charity reach families who need support the most.</p>
    <div class="meta"><span class="btn">Read More</span><span>No Comments</span></div></div>
  </article>
  <article class="post">
    <div class="photo" role="img" aria-label="Young player kicking a ball" style="background:linear-gradient(135deg,#c9a36a,#7aa64a)"></div>
    <div><p>Thanks to our volunteers and families, this year we passed a new giving milestone and opened three more free training spots for kids.</p>
    <div class="meta"><span class="btn">Read More</span><span>No Comments</span></div></div>
  </article>
  <span class="btn more">Read More Blogs</span>
</section>

<section class="block panel news">
  <div class="bar">News</div>
  <div class="news-item"><div class="photo" role="img" aria-label="Hands holding donated coins" style="background:linear-gradient(135deg,#c9b08a,#8a6a45)"></div><p>Fall fundraising match set for the downtown fields.<small>Posted by, Jul 21 2014</small></p></div>
  <div class="news-item"><div class="photo" role="img" aria-label="Hands joined together" style="background:linear-gradient(135deg,#d4b595,#9b7755)"></div><p>New partner charity joins our giving program.<small>Posted by, Jul 14 2014</small></p></div>
  <div class="news-item"><div class="photo" role="img" aria-label="Volunteers sorting supplies" style="background:linear-gradient(135deg,#a8c3d8,#6a8fb0)"></div><p>Summer coaching clinic registration now open.<small>Posted by, Jul 02 2014</small></p></div>
  <span class="btn more">Read More News</span>
</section>

<section class="block appeal" role="img" aria-label="Illustration of a smiling child with a soccer ball on a sunny field">
  <div class="appeal-copy">Participating in developing young players and helping others at the same time.<br><span class="btn green">DONATE NOW</span></div>
</section>

<h2 class="block section-title videos-title">Videos</h2>
<section class="block videos">
  <div class="video-main" role="img" aria-label="Video still of children at a community event">
    <svg class="play" viewBox="0 0 56 56"><circle cx="28" cy="28" r="27" fill="rgba(0,0,0,.45)"/><polygon points="22,17 40,28 22,39" fill="#fff"/></svg>
  </div>
  <div class="video-thumbs">
    <div class="photo" role="img" aria-label="Video thumbnail of a match" style="background:#7aa64a"></div>
    <div class="photo" role="img" aria-label="Video thumbnail of team training" style="background:#9bb86a"></div>
    <div class="photo" role="img" aria-label="Video thumbnail of players on the field" style="background:#6f9a33"></div>
    <div class="photo" role="img" aria-label="Video thumbnail of a goal kick" style="background:#8cb84a"></div>
  </div>
  <span class="btn">SEE VIDEOS</span>
</section>

<h2 class="block section-title gallery-title">Picture Gallery</h2>
<section class="block panel gallery">
  <div class="gallery-main" role="img" aria-label="Photo of players in red kits chasing the ball">
    <span class="arrow prev"></span><span class="arrow next"></span>
  </div>
  <div class="gallery-grid">
    <div class="photo" role="img" aria-label="Gallery photo" style="background:#7aa64a"></div>
    <div class="photo" role="img" aria-label="Gallery photo" style="background:#b85a4a"></div>
    <div class="photo" role="img" aria-label="Gallery photo" style="background:#8cb84a"></div>
    <div class="photo" role="img" aria-label="Gallery photo" style="background:#6a8fb0"></div>
    <div class="photo" role="img" aria-label="Gallery photo" style="background:#9bb86a"></div>
    <div class="photo" role="img" aria-label="Gallery photo" style="background:#6a8fb0"></div>
    <div class="photo" role="img" aria-label="Gallery photo" style="background:#6f9a33"></div>
    <div class="photo" role="img" aria-label="Gallery photo" style="background:#8cb84a"></div>
    <div class="photo" role="img" aria-label="Gallery photo" style="background:#b85a4a"></div>
    <div class="photo" role="img" aria-label="Gallery photo" style="background:#7aa64a"></div>
  </div>
</section>

<h2 class="block board-title">Board Members</h2>
<section class="block board">
  <div class="member"><div class="photo" role="img" aria-label="Portrait of a board member"></div><h3>Dana Whitfield</h3><small>Location</small></div>
  <div class="member"><div class="photo" role="img" aria-label="Portrait of a board member"></div><h3>Dana Whitfield</h3><small>Location</small></div>
  <div class="member"><div class="photo" role="img" aria-label="Portrait of a board member"></div><h3>Dana Whitfield</h3><small>Location</small></div>
  <div class="member"><div class="photo" role="img" aria-label="Portrait of a board member"></div><h3>Dana Whitfield</h3><small>Location</small></div>
  <div class="member"><div class="photo" role="img" aria-label="Portrait of a board member"></div><h3>Dana Whitfield</h3><small>Location</small></div>
  <div class="member"><div class="photo" role="img" aria-label="Portrait of a board member"></div><h3>Dana Whitfield</h3><small>Location</small></div>
</section>

<footer class="block footer">
  <div class="col"><h3>Quick Links</h3>
    <ul><li>Home</li><li>About Us</li><li>Training Programs</li><li>Events</li><li>Faqs</li><li>Contact Us</li></ul></div>
  <div class="col"><h3>Upcoming Events</h3>
    <div class="event"><span class="date"></span><p>Charity match day on the north fields with family games.</p></div>
    <div class="event"><span class="date"></span><p>Youth skills clinic and fundraising walk downtown.</p></div>
    <div class="event"><span class="date"></span><p>Season awards night honoring players and donors.</p></div></div>
  <div class="col contact"><h3>Contact Us</h3>
    <p>Lena Hartwell</p><p>42 Willow Court</p><p>Des Moines, IA</p><p>Telephone: (555) 014 2290</p><p>hello@brightnetrally.org</p></div>
  <div class="col"><h3>Location</h3>
    <div class="map" role="img" aria-label="Street map showing the organization's location"></div></div>
</footer>

<p class="block copyright">© 2014 Bright Net Rally. All Right Reserved</p>

</body>
</html>
```